Website for a financial survey consultancy

WHO WE ARE
We're a niche HR consultancy specialising in salary comparison surveys for the financial asset management industry. We position ourselves as a small, highly responsive organisation with a strong personal relationship with each of our 50+ blue-chip clients.

WHAT WE DO
Our business is 80% surveys (= products), 20% consultancy (= services). The surveys are a set of online products which clients interact with to find the information they are interested in.

WHAT WE WANT
We are completely revising our existing marketing website and need a new up-to-date look and feel for the site. We want you to design 2 web pages
- Home page
- Internal content page

More details below in Must Have Priorities.

REFERENCE SITES
- www.veltramoor.com - nice background image
- www.plimweather.com - ignoring the animations
- www.gasketvale.com
- www.quorbin.com - clean, fresh, styly but prob not corporate enough
- www.dulveropinex.com - spacious, beautiful, slightly dated tho
- www.tambly.co.uk - ignore the colours. Like the simplicity, larger font size (although want to stick with sans-serif fonts for main content)

DELIVERABLES
The final designs should be delivered as one or more PSD files with clearly named layers. All design elements and treatments should be separated out, for example use adjustment layers rather than applied (and subsequently irreversible) adjustments, strokes, shading, etc.

WHAT NEXT
I'll be monitoring the contest every day and can respond to questions fast. You can IM me on Chatterlyne or QBX.

Reason: Hi folks,

I am extending the deadline to this project as I am travelling this week and therefore will not be able to make a final decision until next Monday. I will try and provide further feedback over the course of this week but I am only going to be online occasionally so be prepared to wait a few days for a reply from me.

Thanks for all the designs so far.

Tobias

Target Market(s)

In order of importance, most important first

1. Potential customers - UK & US financial industry HR professionals, short on time. Heard about us already, want to find out more about what we do, confirm relevance for their needs. Core goal - establish credibility: are we properly resourced, will we be around for years to come, are we *real*.

2. Existing customers - UK & US financial industry professionals, short on time, under pressure, want results quickly, minimum faff, expect high quality, slickly presented information. Primary action: login and use surveys.

3. Industry professionals/researchers - probably arriving through blog content, looking to browse and hoover information. Valuable for their ability to spread awareness of who we are amongst their peers.

Industry/Entity Type

Financial

Requirements
Must have
• GENERAL
Style cues - Corporate, professional, financial, stylish, slick, clean, spacious, light
Size - standard 960px grid

NAVIGATION
- [ Home | About us | Surveys | Consulting | Blog ]
- Sub-nav (roll-over dropdown) on About Us, Surveys & Consulting

ALL PAGES
- Site navigation
- Client login (on screen permanently or link to ajaxy in-page pop-up)
- Footer section
- Existing logo (attached)* - this is obviously an important reference point in the design, esp colour

HOME PAGE
- Communicate (link thru to?) survey/consulting split
- Large photo(s)/backdrop (2-3 interchangeable options ideally). Please consider what rights agreement will be necessary for any photos you include in your design.
- Possibly bigger more prominent version of logo
- Strap line/sentence - "Focussed data is the key to success"
- 3 recent blog posts (should look good with and without blog post images)
- Free downloadable PDF research report + supporting blurb

INTERNAL PAGE
- Page title
- Content - typical page will be less than one screenfull
- Level 1 sub-heading
- Level 2 sub-heading
- Bulleted list
- Content supporting image (any image will do - interested in placement, borders (if any), spacing, caption, etc)
- 'Do something' button

* Note: there is some internal debate about this logo at the moment. Some (me) are keen for it to change, some (not me!) are not. If you have an web page design idea/concept that requires an evolution of the logo, go ahead and evolve it. We can explore this further in the design process as necessary, but don't sweat it.
Nice to have
• Values to communicate
- Knowledgeable
- Professional
- Secure
- Personal
- Experienced
- Financial industry specific
- Accurate
- Reliable
Should not have
• - Search box
- Social media links, other than RSS feed button (discrete)

```html
<!DOCTYPE html>
<html lang="en">
<head>
<meta charset="utf-8">
<title>Corvane Consulting – Home</title>
<link rel="stylesheet" href="https://fonts.googleapis.com/css2?family=Arimo:wght@400;700&family=Comfortaa:wght@400&family=Pathway+Gothic+One&display=swap">
<style>
  :root {
    --brand: #6b0c0c;
    --page: #f4f3f1;
    --text: #4a4a4a;
    --muted: #666;
    --footer: #d1cfca;
    --bubble: #b7b5b0;
    --rule: #c9c4bb;
    --frame: #cfcfcf;
    --heading-dark: #3f3f3f;
  }
  * { box-sizing: border-box; margin: 0; padding: 0; }
  html, body { width: 1200px; height: 1144px; overflow: hidden; }
  body { background: var(--page); font-family: "Arimo", Arial, sans-serif; color: var(--text); position: relative; }
  .abs { position: absolute; }

  /* Navigation */
  .main-nav { position: absolute; top: 0; left: 577px; height: 65px; display: flex; }
  .main-nav a { display: block; height: 65px; line-height: 78px; padding: 0 17px; font-size: 16px; color: #555; text-decoration: none; }
  .main-nav a.is-active { background: var(--brand); color: #fff; }

  /* Brand block */
  .brand-square { left: 119px; top: 65px; width: 140px; height: 135px; background: var(--brand); }
  .brand-name { left: 119px; top: 214px; width: 140px; font-size: 34px; color: var(--brand); text-align: center; }

  /* Hero */
  .hero-frame { left: 269px; top: 65px; width: 812px; height: 295px; background: var(--frame); padding: 5px; box-shadow: 60px 8px 12px -8px rgba(0,0,0,.15); }
  .hero-photo { width: 802px; height: 285px; position: relative; overflow: hidden;
    background: linear-gradient(180deg, #b08a48 0%, #e8c06a 35%, #d89a3c 52%, #8a6a4a 70%, #4e4540 100%); }
  .hero-photo::before { content: ""; position: absolute; left: 0; top: 0; width: 380px; height: 100%;
    background: linear-gradient(90deg, rgba(50,45,40,.55), rgba(50,45,40,0)); }
  .hero-strap { position: absolute; left: 377px; top: 154px; width: 425px; height: 131px; background: rgba(140,112,78,.55);
    font-family: "Comfortaa", sans-serif; font-size: 31px; color: #f3dcac; text-align: center; line-height: 128px; }

  /* Company profile */
  .section-title { font-weight: 400; color: var(--brand); }
  .profile-title { left: 119px; top: 398px; font-size: 37px; }
  .profile-copy { left: 119px; top: 447px; width: 662px; font-size: 14px; line-height: 18px; }
  .profile-copy p + p { margin-top: 17px; }

  .download-rule { left: 823px; top: 405px; width: 2px; height: 155px; background: linear-gradient(180deg, transparent, #c4c4c4 30%, #c4c4c4 70%, transparent); }
  .download-card { left: 825px; top: 440px; width: 256px; height: 84px; border-radius: 0 8px 8px 0;
    background: linear-gradient(180deg, #fbfbfb 0%, #e8e8e8 45%, #d6d6d6 100%); }
  .download-icon { position: absolute; left: 27px; top: 13px; width: 58px; height: 62px; background: var(--brand); }
  .download-label { position: absolute; left: 100px; top: 16px; font-family: "Pathway Gothic One", sans-serif; color: #333; }
  .download-label strong { display: block; font-weight: 400; font-size: 30px; line-height: 30px; }
  .download-label span { display: block; font-size: 18px; line-height: 20px; }

  .dotted-divider { left: 119px; top: 584px; width: 959px; border-top: 1px dotted var(--rule); }

  /* Services */
  .service { top: 613px; width: 455px; }
  .service-title { font-size: 30px; height: 48px; }
  .service-body { display: flex; gap: 7px; }
  .service-photo { width: 218px; height: 145px; border: 1px solid #bbb; flex: none; }
  .photo-survey { background: linear-gradient(135deg, #f2f2f2, #cfcfcf 60%, #e6e6e6); }
  .photo-signpost { background: linear-gradient(180deg, #8e8e8e 0%, #c9c9c9 50%, #efefef 100%); }
  .service-text { font-size: 12px; line-height: 15px; letter-spacing: .3px; text-align: justify; color: var(--text); position: relative; width: 230px; padding-top: 1px; }
  .service-text p + p { margin-top: 15px; }
  .read-more { position: absolute; right: 0; top: 138px; color: var(--brand); font-size: 12px; text-decoration: underline; }
  .service-split { left: 597px; top: 620px; height: 190px; border-left: 1px dotted var(--rule); }

  /* Footer */
  .site-footer { left: 0; top: 844px; width: 1200px; height: 300px; background: var(--footer); }
  .footer-title { font-size: 28px; font-weight: 400; color: var(--heading-dark); }
  .blog-bubble { left: 119px; top: 946px; width: 483px; height: 166px; background: var(--bubble); padding: 22px 20px 0;
    box-shadow: inset 0 0 0 2px rgba(0,0,0,.04); font-size: 12px; line-height: 19px; color: #555; }
  .blog-bubble li { list-style: none; margin-bottom: 18px; }
  .bubble-notch { left: 185px; top: 918px; }
  .footer-split { top: 875px; height: 240px; border-left: 1px solid #b8b5ae; box-shadow: 1px 0 0 #e6e4df; }
  .sitemap { left: 698px; top: 914px; font-size: 12px; line-height: 18.8px; color: #555; list-style: none; }
  .sitemap li { font-weight: 700; }
  .sitemap .sub { font-weight: 400; padding-left: 8px; }
  .contact-info { left: 910px; top: 915px; font-size: 12px; line-height: 15px; color: #555; font-style: normal; }
  .contact-rule { left: 909px; top: 1035px; width: 171px; border-top: 1px solid #b8b5ae; }
  .copyright { left: 910px; top: 1100px; font-size: 10px; color: #444; }
</style>
</head>
<body>

<nav class="main-nav">
  <a href="#" class="is-active">Home</a>
  <a href="#">About us</a>
  <a href="#">Surveys</a>
  <a href="#">Consulting</a>
  <a href="#">Blog</a>
  <a href="#">Login</a>
</nav>

<div class="abs brand-square"></div>
<div class="abs brand-name">Corvane</div>

<div class="abs hero-frame">
  <div class="hero-photo" role="img" aria-label="Lighthouse on a rocky shore at sunset">
    <div class="hero-strap">Guiding you to Success</div>
  </div>
</div>

<h1 class="abs section-title profile-title">Company Profile</h1>
<div class="abs profile-copy">
  <p>Lorem Ipsum is simply dummy text of the printing and typesetting industry. Lorem Ipsum has been the industry's standard dummy text.</p>
  <p>When an unknown printer took a galley of type and scrambled it to make a type specimen book. It has survived not only five centuries, but also the leap into electronic typesetting, remaining essentially un-changed.</p>
</div>

<div class="abs download-rule"></div>
<a href="#" class="abs download-card">
  <span class="download-icon"></span>
  <span class="download-label"><strong>Download</strong><span>research report</span></span>
</a>

<div class="abs dotted-divider"></div>

<section class="abs service" style="left:119px">
  <h2 class="section-title service-title">Surveys</h2>
  <div class="service-body">
    <div class="service-photo photo-survey" role="img" aria-label="Pen resting on a survey answer sheet"></div>
    <div class="service-text">
      <p>Lorem Ipsum is simply dummy text of the printing and typesetting industry. Lorem Ipsum has been the industry's standard dummy text.</p>
      <p>When an unknown printer took a galley of type and scrambled it to make a type specimen book.</p>
      <a href="#" class="read-more">read more</a>
    </div>
  </div>
</section>

<div class="abs service-split"></div>

<section class="abs service" style="left:620px">
  <h2 class="section-title service-title">Consultancy</h2>
  <div class="service-body">
    <div class="service-photo photo-signpost" role="img" aria-label="Signpost pointing to support, help, advice, guidance and assistance against a cloudy sky"></div>
    <div class="service-text">
      <p>Lorem Ipsum is simply dummy text of the printing and typesetting industry. Lorem Ipsum has been the industry's standard dummy text.</p>
      <p>When an unknown printer took a galley of type and scrambled it to make a type specimen book.</p>
      <a href="#" class="read-more">read more</a>
    </div>
  </div>
</section>

<footer class="abs site-footer"></footer>

<h3 class="abs footer-title" style="left:119px;top:870px">Blog</h3>
<svg class="abs bubble-notch" width="40" height="29" viewBox="0 0 40 29"><polygon points="0,0 35,28 0,28" fill="#b7b5b0"/></svg>
<ul class="abs blog-bubble">
  <li>• Lorem Ipsum is simply dummy text of the printing and typesetting industry. Lorem Ipsum has been the industry's standard dummy text.</li>
  <li>• When an unknown printer took a galley of type and scrambled it to make a type specimen book.</li>
  <li>• It has survived not only five but also the leap into electronic.</li>
</ul>

<div class="abs footer-split" style="left:646px"></div>

<h3 class="abs footer-title" style="left:697px;top:870px">Sitemap</h3>
<ul class="abs sitemap">
  <li>Home</li>
  <li>About Us</li>
  <li class="sub">Sub Page1</li>
  <li class="sub">Sub Page2</li>
  <li>Surveys</li>
  <li class="sub">Sub Page1</li>
  <li class="sub">Sub Page2</li>
  <li>Consulting</li>
  <li class="sub">Sub Page1</li>
  <li>Blog</li>
  <li>Contact</li>
</ul>

<div class="abs footer-split" style="left:851px"></div>

<h3 class="abs footer-title" style="left:909px;top:870px">Contact</h3>
<address class="abs contact-info">
  Corvane Consulting Ltd<br>
  14 Milbrook Lane<br>
  London EC2N 7QA<br><br>
  +44 (0)20 7946 0321<br>
  info@corvaneconsulting.com
</address>
<div class="abs contact-rule"></div>
<svg class="abs" style="left:909px;top:1056px" width="27" height="27" viewBox="0 0 27 27" aria-label="Copyright">
  <circle cx="13.5" cy="13.5" r="11.5" fill="none" stroke="#444" stroke-width="2.4"/>
  <path d="M17.5 10.2a5 5 0 1 0 0 6.6" fill="none" stroke="#444" stroke-width="2.4"/>
</svg>
<div class="abs copyright">2011 Copyright corvaneconsulting.com</div>

</body>
</html>
```